Webdesign Hauskranken- und Tagespflege „Am Lindenhof“
Zielgruppe
Die Hauskranken- und Tagespflege „Am Lindenhof“ in Plauen ist ein unabhängiges, privat geführtes Unternehmen im Bereich der ambulanten und teilstationären Kranken- und Seniorenpflege. Seit der Gründung am 1. März 2009 stehen wir für eine zuverlässige, individuelle und herzliche Betreuung unserer Klientinnen und Klienten.
Das Team ist ein engagiertes Pflegeteam und auf über 35 qualifizierte Mitarbeiterinnen und Mitarbeiter angewachsen. Gemeinsam setzen wir uns täglich dafür ein, Menschen mit Pflegebedarf eine bestmögliche Versorgung und ein hohes Maß an Lebensqualität zu ermöglichen.
Unsere Firmenphilosophie basiert auf Wertschätzung, Vertrauen und Respekt – sowohl im Umgang mit unseren Klientinnen und Klienten sowie deren Angehörigen als auch innerhalb unseres Teams. Eine persönliche, einfühlsame und fachlich kompetente Betreuung steht für uns an erster Stelle.
Ob Grundpflege oder Behandlungspflege – bei uns sind Sie in guten Händen. Wir begleiten unsere Klientinnen und Klienten mit Fürsorge, Fachkompetenz und Herz und unterstützen sie dabei, ihren Alltag so selbstbestimmt wie möglich zu gestalten.
Gleichzeitig entlasten wir Angehörige, Freunde und Bekannte, indem wir ihnen Sicherheit geben und Freiräume schaffen. So bleibt mehr Zeit für gemeinsame, unbeschwerte Momente mit den Menschen, die ihnen am Herzen liegen.
Unsere Tagespflege bietet Platz für 18 Gäste. Der große Aufenthaltsraum mit offener Küche lädt zum gemütlichen Beisammensein ein. In unserem Ruheraum können sich unsere Gäste bei Bedarf zurückziehen und sich ausruhen, auch Therapien (Logopädie, Ergotherapie, Physiotherapie…) werden darin durchgeführt. Der Aufenthaltsraum ist zum Teil eingerichtet wie eine gemütliche Wohnstube, ihre Einrichtung erinnert an frühere Zeiten. Gemütliche Ruhesessel laden zum Entspannen ein.
Der persönliche Kontakt und das Vertrauen unserer Patientinnen und Patienten bilden dabei st..
Aufgabenstellung
Ziele des Relaunchs:
modernes, freundliches und barrierearmes Design
klare Benutzerführung für Senioren und Angehörige
Hinweis zum Rückrufservice
Notfallnummer dauerhaft sichtbar
schnelle Kontaktaufnahme (Telefon, Rückruf, Kontaktformular)
bessere Auffindbarkeit bei Google (SEO)
Vertrauen durch authentische Bilder, Teamvorstellung und Bewertungen

```html
<!DOCTYPE html>
<html lang="de">
<head>
<meta charset="utf-8">
<title>Hauskranken- und Tagespflege „Am Lindenhof“ – Plauen</title>
<link rel="stylesheet" href="https://fonts.googleapis.com/css2?family=Inter:wght@400;500;600;700;800&display=swap">
<style>
:root{
  --navy:#1d3f5e;
  --navy-deep:#1b3a58;
  --blue:#1a5f86;
  --blue-btn:#1c5b82;
  --yellow:#fcdc4f;
  --yellow-soft:#fbeaa0;
  --ice:#e6f1f8;
  --cream:#fdf8ec;
  --text:#3c4a57;
  --muted:#6b7884;
  --line:#dfe5ea;
  --white:#ffffff;
}
*{box-sizing:border-box;margin:0;padding:0}
html,body{width:1200px;height:5148px;overflow:hidden}
body{font-family:"Inter",sans-serif;color:var(--text);background:var(--white);font-size:14px;line-height:1.6}
.wrap{width:916px;margin:0 auto;position:relative;height:100%}
svg.ic{width:18px;height:18px;fill:none;stroke:currentColor;stroke-width:2;stroke-linecap:round;stroke-linejoin:round;flex:none}
section,header,footer,.topbar{position:relative}

.topbar{height:32px;background:var(--navy);color:#dbe4ec;font-size:11px}
.topbar .wrap{display:flex;align-items:center;justify-content:space-between}
.topbar span{display:flex;align-items:center;gap:6px}
.topbar svg.ic{width:12px;height:12px}
.topbar .emergency{color:var(--yellow);font-weight:600}

.site-header{height:60px;background:var(--white);border-bottom:1px solid var(--line)}
.site-header .wrap{width:990px;display:flex;align-items:center;justify-content:space-between}
.brand{display:flex;align-items:center;gap:8px;font-weight:700;color:var(--navy);font-size:13px}
.brand i{width:26px;height:26px;border-radius:50%;background:var(--yellow);display:block}
.nav{display:flex;align-items:center;gap:26px;font-size:13px;font-weight:500;color:var(--navy)}
.btn{display:inline-flex;align-items:center;gap:8px;font-weight:700;font-size:13px;border-radius:6px;padding:0 18px;height:38px;text-decoration:none}
.btn-yellow{background:var(--yellow);color:var(--navy)}
.btn-ghost{border:1.5px solid rgba(255,255,255,.7);color:#fff}
.btn-navy{background:var(--blue-btn);color:#fff}
.btn svg.ic{width:14px;height:14px}

.hero{height:598px;overflow:hidden}
.hero-photo{position:absolute;inset:0;background:linear-gradient(100deg,#8a8f94 0%,#b8b4ad 40%,#d7cfbf 62%,#c9a65a 78%,#d9d4cc 100%)}
.hero-shade{position:absolute;inset:0;background:linear-gradient(90deg,rgba(29,63,94,.88) 0%,rgba(29,63,94,.7) 40%,rgba(29,63,94,.1) 70%,rgba(29,63,94,0) 100%)}
.hero .wrap{padding-top:152px}
.badge{display:inline-block;background:var(--yellow);color:var(--navy);font-size:11px;font-weight:700;padding:3px 10px;border-radius:20px}
.hero h1{color:#fff;font-size:40px;line-height:1.22;font-weight:700;margin-top:14px;letter-spacing:-.5px}
.hero p{color:#e5ecf2;font-size:15px;line-height:1.7;width:550px;margin-top:18px}
.hero .actions{display:flex;gap:14px;margin-top:24px}

.infobar{height:70px;background:var(--yellow);color:var(--navy)}
.infobar .wrap{display:flex;align-items:center;justify-content:space-between;padding-right:40px}
.info{display:flex;align-items:center;gap:12px;font-size:12px;line-height:1.45;font-weight:500}
.info b{font-size:13px;font-weight:700}

.callback{height:86px;background:var(--ice)}
.callback .wrap{display:flex;align-items:center;justify-content:space-between}
.callback p{width:700px;font-size:13px;color:var(--text)}
.callback p b{color:var(--navy)}

.about{height:564px}
.about h2,.sec-title{color:var(--navy);font-size:30px;line-height:1.18;font-weight:700;letter-spacing:-.4px}
.about .text{position:absolute;left:0;top:68px;width:444px}
.about .text p{font-size:13.5px;line-height:1.78;margin-top:14px}
.stats{display:flex;gap:14px;margin-top:26px}
.stat{width:138px;height:74px;border:1px solid var(--line);border-radius:12px;text-align:center;padding-top:12px}
.stat b{display:block;color:var(--blue);font-size:20px;font-weight:700}
.stat span{font-size:11px;color:var(--muted)}
.photo-card{position:absolute;background:#fff;border-radius:12px;box-shadow:0 8px 24px rgba(29,63,94,.14);overflow:hidden;width:212px}
.photo-card .ph{height:184px}
.photo-card figcaption{padding:14px 12px;font-size:12px;font-weight:600;color:var(--navy);line-height:1.5;height:88px}

.services{height:510px;background:var(--cream)}
.services .lead{font-size:14px;color:var(--muted);margin-top:10px}
.sec-head{padding-top:64px}
.cards{display:grid;grid-template-columns:448px 448px;gap:20px;margin-top:34px}
.card{background:#fff;border:1px solid #ece6d4;border-radius:12px;padding:20px 18px 18px 72px;position:relative;height:134px}
.card .ico{position:absolute;left:20px;top:20px;width:34px;height:34px;border-radius:50%;background:var(--ice);color:var(--blue);display:flex;align-items:center;justify-content:center}
.card h3{color:var(--navy);font-size:16px;font-weight:700}
.card p{font-size:12.5px;line-height:1.7;margin-top:6px}

.values{height:476px;background:linear-gradient(160deg,var(--navy-deep) 0%,#1a4d72 60%,#176790 100%);color:#fff}
.values .sec-title{color:#fff}
.values .lead{font-size:14px;line-height:1.7;width:610px;margin-top:16px;color:#dce6ee}
.vgrid{display:grid;grid-template-columns:repeat(3,292px);gap:20px;margin-top:46px}
.vcard{background:rgba(255,255,255,.1);border-radius:12px;padding:20px 20px;height:172px}
.vcard .ico{color:var(--yellow)}
.vcard .ico svg.ic{width:22px;height:22px}
.vcard h3{font-size:16px;font-weight:700;margin-top:14px}
.vcard p{font-size:12.5px;line-height:1.7;margin-top:8px;color:#d4e0ea}

.daycare{height:566px}
.daycare .ph{position:absolute;left:0;top:66px;width:442px;height:404px;border-radius:14px;background:linear-gradient(135deg,#e9e6e2 0%,#d9cbc0 45%,#a4a6ad 75%,#c7c0b7 100%);box-shadow:0 10px 26px rgba(0,0,0,.12)}
.daycare .text{position:absolute;left:474px;top:64px;width:442px}
.daycare .text p{font-size:13.5px;line-height:1.78;margin-top:14px}
.ticks{list-style:none;margin-top:18px}
.ticks li{display:flex;align-items:center;gap:10px;font-size:13.5px;margin-bottom:10px}
.ticks svg.ic{width:16px;height:16px;color:var(--blue)}
.daycare .btn{margin-top:14px}

.people{height:428px;background:var(--ice)}
.people .text{position:absolute;left:0;top:78px;width:442px}
.people .text p{font-size:13.5px;line-height:1.78;margin-top:18px}
.team-line{display:flex;align-items:center;gap:10px;margin-top:18px;font-size:13.5px;font-weight:600;color:var(--navy)}
.team-line svg.ic{color:var(--blue);width:16px;height:16px}
.hiring{margin-top:20px;background:var(--yellow-soft);border-radius:8px;height:48px;display:flex;align-items:center;padding:0 16px;font-weight:600;color:var(--navy);font-size:13.5px}
.people .ph{position:absolute;left:474px;top:78px;width:442px;height:332px;border-radius:14px;background:linear-gradient(125deg,#e8e2d8 0%,#d7c7a7 35%,#7e6a58 60%,#b9b2a6 100%)}

.reviews{height:510px}
.reviews .sec-head{padding-top:94px}
.rgrid{display:grid;grid-template-columns:repeat(3,292px);gap:20px;margin-top:36px}
.review{border:1px solid var(--line);border-radius:10px;padding:16px 20px;height:200px;position:relative}
.stars{color:var(--yellow);letter-spacing:2px;font-size:15px}
.review blockquote{font-size:13.5px;line-height:1.78;margin-top:8px;color:var(--text)}
.review cite{position:absolute;left:20px;bottom:20px;font-style:normal;font-size:12px;font-weight:600;color:var(--blue)}

.contact{height:770px;background:var(--cream)}
.contact .text{position:absolute;left:0;top:128px;width:430px}
.contact .text>p{font-size:13.5px;line-height:1.78;margin-top:16px}
.clist{list-style:none;margin-top:34px}
.clist li{display:flex;gap:14px;margin-bottom:26px;font-size:13.5px;line-height:1.6}
.clist svg.ic{color:var(--blue);margin-top:2px}
.clist b{color:var(--navy);display:block;font-weight:700}
.clist .row{display:flex;gap:56px}
.clist .phone{color:var(--blue);font-weight:700;font-size:15px}
.form{position:absolute;left:474px;top:110px;width:442px;background:#fff;border-radius:14px;box-shadow:0 8px 24px rgba(29,63,94,.1);padding:26px 26px 24px}
.form h3{color:var(--navy);font-size:16px;font-weight:700}
.form .sub{font-size:12px;color:var(--muted);margin-top:4px}
.field{margin-top:20px}
.field label{display:block;font-size:12px;color:var(--navy);font-weight:500;margin-bottom:8px}
.field .in{height:38px;border:1px solid var(--line);border-radius:6px;font-size:11px;color:#9aa4ad;padding:0 10px;display:flex;align-items:center}
.field .ta{height:82px}
.form .btn{width:100%;justify-content:center;margin-top:20px;height:42px}
.form .note{font-size:10.5px;color:var(--muted);margin-top:14px;white-space:nowrap}

.site-footer{height:478px;background:var(--navy);color:#c6d3de;font-size:11px}
.fbrand{position:absolute;left:0;top:96px}
.fbrand .mark{display:flex;align-items:center;gap:12px;color:#fff;font-weight:700;font-size:20px}
.fbrand .mark i{width:40px;height:40px;border-radius:50%;background:var(--yellow);display:block}
.fbrand p{margin-top:64px;line-height:1.6}
.fname{position:absolute;left:364px;top:196px;width:280px}
.fname b{display:block;color:#fff;font-size:13px;line-height:1.55}
.fname span{display:block;margin-top:10px}
.fcall{position:absolute;right:0;top:196px;font-size:13px;color:#fff}
.fcall b{color:var(--yellow)}
.fbottom{position:absolute;left:0;right:0;top:392px;display:flex;justify-content:space-between}
.fbottom nav{display:flex;gap:20px}
</style>
</head>
<body>

<svg width="0" height="0" style="position:absolute">
  <defs>
    <symbol id="i-phone" viewBox="0 0 24 24"><path d="M22 16.9v3a2 2 0 0 1-2.2 2 19.8 19.8 0 0 1-8.6-3.1 19.5 19.5 0 0 1-6-6A19.8 19.8 0 0 1 2.1 4.2 2 2 0 0 1 4.1 2h3a2 2 0 0 1 2 1.7c.1 1 .4 1.9.7 2.8a2 2 0 0 1-.5 2.1L8 9.9a16 16 0 0 0 6 6l1.3-1.3a2 2 0 0 1 2.1-.4c.9.3 1.8.6 2.8.7a2 2 0 0 1 1.7 2z"/></symbol>
    <symbol id="i-pin" viewBox="0 0 24 24"><path d="M20 10c0 6-8 12-8 12s-8-6-8-12a8 8 0 0 1 16 0z"/><circle cx="12" cy="10" r="3"/></symbol>
    <symbol id="i-clock" viewBox="0 0 24 24"><circle cx="12" cy="12" r="10"/><path d="M12 6v6l4 2"/></symbol>
    <symbol id="i-heart" viewBox="0 0 24 24"><path d="M20.8 4.6a5.5 5.5 0 0 0-7.8 0L12 5.7l-1-1.1a5.5 5.5 0 0 0-7.8 7.8l1 1.1L12 21l7.8-7.5 1-1.1a5.5 5.5 0 0 0 0-7.8z"/></symbol>
    <symbol id="i-steth" viewBox="0 0 24 24"><path d="M5 3v6a5 5 0 0 0 10 0V3"/><path d="M10 14v2a5 5 0 0 0 10 0v-2"/><circle cx="20" cy="12" r="2"/></symbol>
    <symbol id="i-home" viewBox="0 0 24 24"><path d="M3 10l9-7 9 7v10a2 2 0 0 1-2 2H5a2 2 0 0 1-2-2z"/><path d="M9 22V12h6v10"/></symbol>
    <symbol id="i-sun" viewBox="0 0 24 24"><circle cx="12" cy="12" r="4"/><path d="M12 2v2M12 20v2M4.9 4.9l1.4 1.4M17.7 17.7l1.4 1.4M2 12h2M20 12h2M4.9 19.1l1.4-1.4M17.7 6.3l1.4-1.4"/></symbol>
    <symbol id="i-hand" viewBox="0 0 24 24"><path d="M11 14h2a2 2 0 0 0 0-4h-3c-.6 0-1.1.2-1.4.6L3 16"/><path d="M7 20l1.6-1.4c.3-.4.8-.6 1.4-.6h4c1.1 0 2.1-.4 2.8-1.2l4.6-4.4a2 2 0 0 0-2.8-2.8l-4.2 3.9"/></symbol>
    <symbol id="i-shield" viewBox="0 0 24 24"><path d="M12 22s8-4 8-10V5l-8-3-8 3v7c0 6 8 10 8 10z"/><path d="M9 12l2 2 4-4"/></symbol>
    <symbol id="i-spark" viewBox="0 0 24 24"><path d="M9.9 15.5 8 21l-1.9-5.5L1 13.6l5.1-1.9L8 6l1.9 5.7 5.1 1.9z"/><path d="M18 2v4M16 4h4M19 15v4M17 17h4"/></symbol>
    <symbol id="i-users" viewBox="0 0 24 24"><path d="M17 21v-2a4 4 0 0 0-4-4H5a4 4 0 0 0-4 4v2"/><circle cx="9" cy="7" r="4"/><path d="M23 21v-2a4 4 0 0 0-3-3.9M16 3.1a4 4 0 0 1 0 7.8"/></symbol>
    <symbol id="i-access" viewBox="0 0 24 24"><circle cx="12" cy="4" r="2"/><path d="M19 13v-2a7 7 0 0 0-7-1 7 7 0 0 0-7 1v2"/><path d="M10 10v6l-3 6M14 10v6l3 6"/></symbol>
  </defs>
</svg>

<div class="topbar">
  <div class="wrap">
    <span><svg class="ic"><use href="#i-clock"/></svg>Mo – Do: 8:30 – 15:30 Uhr | Fr: 8:30 – 13:30 Uhr | und nach Vereinbarung</span>
    <span class="emergency"><svg class="ic"><use href="#i-phone"/></svg>24h-Notruf: 03741 / 459026</span>
  </div>
</div>

<header class="site-header">
  <div class="wrap">
    <div class="brand"><i></i>Am Lindenhof</div>
    <nav class="nav">
      <span>Über uns</span><span>Leistungen</span><span>Tagespflege</span><span>Team</span><span>Bewertungen</span><span>Kontakt</span>
      <a class="btn btn-yellow"><svg class="ic"><use href="#i-phone"/></svg>Rückruf anfordern</a>
    </nav>
  </div>
</header>

<section class="hero">
  <div class="hero-photo" role="img" aria-label="Foto: Pflegerin misst bei einem älteren Herrn zu Hause den Blutdruck"></div>
  <div class="hero-shade"></div>
  <div class="wrap">
    <span class="badge">Ihr Pflegeteam aus Plauen – seit 2009</span>
    <h1>Pflege mit Herz, direkt bei<br>Ihnen in Plauen</h1>
    <p>Hauskrankenpflege und Tagespflege „Am Lindenhof“ – zuverlässig, individuell und herzlich. Damit Sie so selbstbestimmt leben können wie möglich.</p>
    <div class="actions">
      <a class="btn btn-yellow"><svg class="ic"><use href="#i-phone"/></svg>03741 / 459026 anrufen</a>
      <a class="btn btn-ghost">Rückruf anfordern</a>
    </div>
  </div>
</section>

<div class="infobar">
  <div class="wrap">
    <div class="info"><svg class="ic"><use href="#i-phone"/></svg><div>24h-Notruf<br><b>03741 / 459026</b></div></div>
    <div class="info"><svg class="ic"><use href="#i-pin"/></svg><div><b>Lindenweg 28</b><br><b>08523 Plauen</b></div></div>
    <div class="info"><svg class="ic"><use href="#i-clock"/></svg><div><b>Mo – Do: 8:30 – 15:30 Uhr</b><br><b>Fr: 8:30 – 13:30 Uhr</b></div></div>
  </div>
</div>

<div class="callback">
  <div class="wrap">
    <p><b>Rückrufservice:</b> Sie erreichen uns gerade nicht? Hinterlassen Sie Namen und Nummer – wir melden uns garantiert am nächsten Werktag bei Ihnen zurück.</p>
    <a class="btn btn-navy">Zum Rückrufformular</a>
  </div>
</div>

<section class="about">
  <div class="wrap">
    <div class="text">
      <h2>Hauskranken- und<br>Tagespflege „Am Lindenhof“</h2>
      <p>Wir sind ein unabhängiges, privatrechtliches Unternehmen der ambulanten und teilstationären Kranken- und Seniorenpflege in Plauen. Seit unserer Gründung am 1. März 2009 stehen wir für zuverlässige, individuelle und herzliche Betreuung.</p>
      <p>Aus einem kleinen Pflegeteam sind über 35 qualifizierte Mitarbeiterinnen und Mitarbeiter geworden. Ob Grundpflege oder Behandlungspflege – wir begleiten unsere Klienten mit Sorgfalt, Fachwissen und Herz und entlasten gleichzeitig Angehörige, Freunde und Bekannte. So bleibt mehr Zeit für gemeinsame, unbeschwerte Momente.</p>
      <div class="stats">
        <div class="stat"><b>2009</b><span>gegründet</span></div>
        <div class="stat"><b>35+</b><span>Pflegekräfte</span></div>
        <div class="stat"><b>18</b><span>Tagespflegeplätze</span></div>
      </div>
    </div>
    <figure class="photo-card" style="left:474px;top:144px">
      <div class="ph" role="img" aria-label="Foto: Pflegerin bei einem älteren Herrn im Wohnzimmer" style="background:linear-gradient(135deg,#dcd8d2,#a9aeb2 55%,#6f7f86)"></div>
      <figcaption>Hauskrankenpflege in Ihrem Zuhause</figcaption>
    </figure>
    <figure class="photo-card" style="left:704px;top:169px">
      <div class="ph" role="img" aria-label="Foto: Pfleger und ältere Dame im Gespräch auf dem Sofa" style="background:linear-gradient(135deg,#cfd4d8,#8d8880 50%,#b7a7a0)"></div>
      <figcaption>Tagespflege in familiärer Runde</figcaption>
    </figure>
  </div>
</section>

<section class="services">
  <div class="wrap">
    <div class="sec-head">
      <h2 class="sec-title">Unsere Leistungen</h2>
      <p class="lead">Für pflegebedürftige Menschen in Plauen und Umgebung – und für ihre Angehörigen.</p>
    </div>
    <div class="cards">
      <div class="card"><span class="ico"><svg class="ic"><use href="#i-steth"/></svg></span><h3>Behandlungspflege</h3><p>Medizinische Leistungen auf Verordnung: Medikamentengabe, Injektionen, Wundversorgung und Blutdruckkontrolle.</p></div>
      <div class="card"><span class="ico"><svg class="ic"><use href="#i-home"/></svg></span><h3>Grundpflege</h3><p>Unterstützung bei Körperpflege, Ernährung, Mobilität und allem, was den Alltag zu Hause leichter macht.</p></div>
      <div class="card"><span class="ico"><svg class="ic"><use href="#i-sun"/></svg></span><h3>Tagespflege</h3><p>18 Plätze, Gemeinschaft, Mahlzeiten, Therapien und Ruheraum – abends geht es zurück ins eigene Zuhause.</p></div>
      <div class="card"><span class="ico"><svg class="ic"><use href="#i-hand"/></svg></span><h3>Entlastung für Angehörige</h3><p>Beratung zu Pflegegraden und Leistungen, Verhinderungspflege und verlässliche Absprachen mit Ihrer Familie.</p></div>
    </div>
  </div>
</section>

<section class="values">
  <div class="wrap">
    <div class="sec-head">
      <h2 class="sec-title">Unser Pflegeleitbild</h2>
      <p class="lead">Unsere Unternehmensphilosophie beruht auf Wertschätzung, Vertrauen und Respekt – gegenüber unseren Klienten und deren Angehörigen ebenso wie innerhalb unseres Teams. Persönliche, einfühlsame und fachlich kompetente Pflege hat für uns oberste Priorität.</p>
    </div>
    <div class="vgrid">
      <div class="vcard"><span class="ico"><svg class="ic"><use href="#i-heart"/></svg></span><h3>Wertschätzung</h3><p>Jeder Mensch wird bei uns mit Respekt und liebevoller Zuwendung versorgt.</p></div>
      <div class="vcard"><span class="ico"><svg class="ic"><use href="#i-shield"/></svg></span><h3>Vertrauen</h3><p>Feste Bezugspflege – Sie kennen die Menschen, die zu Ihnen nach Hause kommen.</p></div>
      <div class="vcard"><span class="ico"><svg class="ic"><use href="#i-spark"/></svg></span><h3>Fachkompetenz</h3><p>Über 35 qualifizierte Mitarbeiterinnen und Mitarbeiter, regelmäßig weitergebildet.</p></div>
    </div>
  </div>
</section>

<section class="daycare">
  <div class="wrap">
    <div class="ph" role="img" aria-label="Foto: Pflegerin reicht einem älteren Paar am Tisch Medikamente"></div>
    <div class="text">
      <h2 class="sec-title">Tagespflege für 18 Gäste</h2>
      <p>Der große Aufenthaltsraum mit offener Küche lädt zum Beisammensein in gemütlicher Atmosphäre ein. Er ist teilweise wie ein behagliches Wohnzimmer eingerichtet – die Möbel erinnern an frühere Zeiten, bequeme Ruhesessel laden zum Entspannen ein.</p>
      <p>Wer Ruhe braucht, kann sich in unseren Entspannungsraum zurückziehen. Dort finden auch Therapien statt – Logopädie, Ergotherapie, Physiotherapie und weitere.</p>
      <ul class="ticks">
        <li><svg class="ic"><use href="#i-heart"/></svg>Frühstück, Mittagessen und Kaffeetrinken in Gesellschaft</li>
        <li><svg class="ic"><use href="#i-heart"/></svg>Gedächtnistraining, Gymnastik und gemeinsame Aktivitäten</li>
        <li><svg class="ic"><use href="#i-heart"/></svg>Fahrdienst von und zur Tagespflege auf Wunsch</li>
      </ul>
      <a class="btn btn-navy">Platz anfragen</a>
    </div>
  </div>
</section>

<section class="people">
  <div class="wrap">
    <div class="text">
      <h2 class="sec-title">Menschen, die für Menschen<br>da sind</h2>
      <p>Persönlicher Kontakt und das Vertrauen unserer Patienten stehen immer im Mittelpunkt unseres Handelns. Unser Team aus Pflegefachkräften, Pflegehelfern, Betreuungskräften und Verwaltung arbeitet jeden Tag daran, pflegebedürftigen Menschen die bestmögliche Versorgung und ein hohes Maß an Lebensqualität zu geben.</p>
      <div class="team-line"><svg class="ic"><use href="#i-users"/></svg>Über 35 qualifizierte Mitarbeiterinnen und Mitarbeiter</div>
      <div class="hiring">Helft denen, die Hilfe brauchen. Mitarbeiter gesucht!</div>
    </div>
    <div class="ph" role="img" aria-label="Foto: Betreuerin und älterer Herr beim gemeinsamen Spiel am Tisch"></div>
  </div>
</section>

<section class="reviews">
  <div class="wrap">
    <div class="sec-head"><h2 class="sec-title">Das sagen Klienten und Angehörige</h2></div>
    <div class="rgrid">
      <div class="review"><div class="stars">★★★★★</div><blockquote>„Meine Mutter wird seit drei Jahren betreut. Immer freundlich, immer pünktlich – und wir als Familie können endlich wieder ruhig schlafen.“</blockquote><cite>Sabine W., Tochter einer Klientin</cite></div>
      <div class="review"><div class="stars">★★★★★</div><blockquote>„In der Tagespflege blüht mein Vater richtig auf. Die Atmosphäre ist wie in einem gemütlichen Wohnzimmer.“</blockquote><cite>Thomas R., Plauen</cite></div>
      <div class="review"><div class="stars">★★★★★</div><blockquote>„Vom ersten Beratungsgespräch bis zur Antragstellung wurde uns alles geduldig erklärt. Sehr herzliches Team.“</blockquote><cite>Renate K., Angehörige</cite></div>
    </div>
  </div>
</section>

<section class="contact">
  <div class="wrap">
    <div class="text">
      <h2 class="sec-title">Wir beraten Sie gern –<br>kostenlos und unverbindlich</h2>
      <p>Rufen Sie uns an oder fordern Sie einen Rückruf an. Wir nehmen uns Zeit für Ihre Fragen zu Pflegegrad, Kosten und Leistungen.</p>
      <ul class="clist">
        <li><svg class="ic"><use href="#i-phone"/></svg><div class="row"><b>24h-Notruf &amp;<br>Beratung</b><span class="phone">03741 / 459026</span></div></li>
        <li><svg class="ic"><use href="#i-pin"/></svg><div><b>Adresse</b>Lindenweg 28, 08523 Plauen</div></li>
        <li><svg class="ic"><use href="#i-clock"/></svg><div><b>Bürozeiten</b>Mo – Do: 8:30 – 15:30 Uhr, Fr: 8:30 – 13:30 Uhr und nach Vereinbarung</div></li>
        <li><svg class="ic"><use href="#i-access"/></svg><div><b>Barrierefrei</b>Große Schrift, klare Kontraste, Bedienung per Tastatur möglich.</div></li>
      </ul>
    </div>
    <form class="form">
      <h3>Rückruf anfordern</h3>
      <p class="sub">Wir melden uns spätestens am nächsten Werktag bei Ihnen.</p>
      <div class="field"><label>Ihr Name</label><div class="in"></div></div>
      <div class="field"><label>Telefonnummer für den Rückruf</label><div class="in"></div></div>
      <div class="field"><label>Wann dürfen wir anrufen? (optional)</label><div class="in">z. B. vormittags</div></div>
      <div class="field"><label>Ihr Anliegen (optional)</label><div class="in ta"></div></div>
      <a class="btn btn-yellow">Kostenlosen Rückruf anfordern</a>
      <p class="note">Ihre Daten werden ausschließlich zur Bearbeitung Ihrer Anfrage verwendet.</p>
    </form>
  </div>
</section>

<footer class="site-footer">
  <div class="wrap">
    <div class="fbrand">
      <div class="mark"><i></i>Am Lindenhof</div>
      <p>© 2026 Am Lindenhof · Kontakt · Datenschutz ·<br>Impressum · Erklärung zur Barrierefreiheit</p>
    </div>
    <div class="fname"><b>Hauskranken- und Tagespflege „Am Lindenhof“</b><span>Lindenweg 28 · 08523 Plauen</span></div>
    <div class="fcall">24h-Notruf: <b>03741 / 459026</b></div>
    <div class="fbottom">
      <span>© 2026 Am Lindenhof</span>
      <nav><span>Kontakt</span><span>Datenschutz</span><span>Impressum</span><span>Erklärung zur Barrierefreiheit</span></nav>
    </div>
  </div>
</footer>

</body>
</html>
```